Existing Website Requiring new Pages

I have an existing word press website that was built using elementor.
Website: www.tallowcrestcare.com.au
I require the Vacancies page (https://www.tallowcrestcare.com.au/vacancies/) to be modified to display our new properties along with minor tweaks to how the information is presented.
The vacancies to be displayed are the exactly the same as those that are located on the homepage of QMR website (https://qmr.org.au/)
The new pages that link off the Vacancies tab will require custom design.
There are roughly 8 pages/properties to be incorporated. i wish for the design to be very similar to that displayed in the following link; https://www.polunda.com.au/vacancies/merrylands
Along with this the back end has not been updated for the last 3 years so it also requires some maintenance.
Website is in the disability industry and the custom pages will display information relative to Property Vacancies.
I have attached a ZIP file with some design guides, the information for each of the properties (which will need to be modified to show our business name Tallowcrest Care) and the example of how it is to look based off the Polunda website.
If you guys have any suggestions or ideas on how to make this more presentable or possible i'm open to your ideas.
Target Market(s)
People looking for SDA properties custom built for people with a disability
Industry/Entity Type
Disability
Coding
Coded - Design and coding required
Number of Pages Required
5+ page

```html
<!DOCTYPE html>
<html lang="en">
<head>
<meta charset="utf-8">
<title>Vacancies – Tallowcrest Care</title>
<link rel="stylesheet" href="https://fonts.googleapis.com/css2?family=Montserrat:wght@400;500;600;700&family=Nunito:wght@400;600&display=swap">
<style>
  :root{
    --teal:#2dd6c4;
    --orange:#f39a6e;
    --ink:#1f1f1f;
    --nav:#333;
    --muted:#8a8f99;
    --line:#e3e6ea;
    --card-border:#d9dcdf;
    --footer-bg:#ffffff;
    --bar:#3b3b3b;
    --blue:#1f7fd6;
    --pink:#e0407b;
  }
  *{box-sizing:border-box;margin:0;padding:0}
  html,body{width:730px;height:1200px;overflow:hidden;background:#fff}
  body{position:relative;font-family:"Montserrat",sans-serif;color:var(--ink)}

  .site-header{position:absolute;left:0;top:0;width:730px;height:73px;background:#fff}
  .brand{position:absolute;left:59px;top:28px;display:flex;align-items:center;gap:6px}
  .brand-dot{width:14px;height:14px;border-radius:50%;background:var(--teal)}
  .brand-name{font-size:13px;font-weight:600;color:var(--teal)}
  .main-nav{position:absolute;right:60px;top:32px;display:flex;gap:19px;font-size:8px;font-weight:600;letter-spacing:.2px;color:var(--nav)}
  .main-nav .active{color:var(--orange)}

  .hero{position:absolute;left:0;top:73px;width:730px;height:316px;overflow:hidden}
  .hero-photo{position:absolute;left:250px;top:0;width:480px;height:316px;
    background:linear-gradient(135deg,#f1eeea 0%,#e3ddd5 40%,#c8b9a4 70%,#8f8f8c 100%)}
  .hero-shape{position:absolute;left:0;top:0}
  .hero-title{position:absolute;left:58px;top:98px;font-size:31px;font-weight:600;color:#fff}

  .vacancy-grid{position:absolute;left:60px;top:451px;display:grid;grid-template-columns:repeat(4,141px);column-gap:15.5px;row-gap:19px}
  .vacancy-card{width:141px;height:209px;border:1px solid var(--card-border);border-radius:4px;background:#fff;box-shadow:0 1px 3px rgba(0,0,0,.06);padding:8px;position:relative}
  .vacancy-photo{width:125px;height:104px;border-radius:4px}
  .ph-1{background:linear-gradient(180deg,#e9ebee 0%,#9a8f82 55%,#5e7a3f 100%)}
  .ph-2{background:linear-gradient(180deg,#cdd4d6 0%,#a07a5a 50%,#6a8c3c 100%)}
  .ph-3{background:linear-gradient(180deg,#4da3e0 0%,#f0e2b4 55%,#7fa84a 100%)}
  .ph-4{background:linear-gradient(180deg,#8fbbe0 0%,#6c7a63 50%,#b9b3a0 100%)}
  .ph-5{background:linear-gradient(180deg,#7fb6e6 0%,#2a2a2e 50%,#4f7a3a 100%)}
  .ph-6{background:linear-gradient(180deg,#7ebbeb 0%,#d7c8ad 50%,#5aa83a 100%)}
  .ph-7{background:linear-gradient(180deg,#86b7e3 0%,#c26a3c 45%,#6aaa3e 100%)}
  .ph-8{background:linear-gradient(180deg,#9cc3e6 0%,#5c5650 50%,#7f9a3a 100%)}
  .vacancy-name{margin-top:14px;font-size:11.5px;font-weight:600;letter-spacing:.1px}
  .vacancy-meta{margin-top:9px;display:flex;align-items:center;gap:5px;font-family:"Nunito",sans-serif;font-size:9px;color:#444}
  .vacancy-meta svg{flex:none}
  .book-btn{position:absolute;left:7px;top:172px;width:77px;height:20px;border:1px solid var(--orange);border-radius:10px;color:var(--orange);font-size:9px;font-weight:600;display:flex;align-items:center;justify-content:center}

  .site-footer{position:absolute;left:0;top:945px;width:730px;height:218px;background:var(--footer-bg);box-shadow:0 -6px 10px rgba(0,0,0,.04)}
  .footer-brand{position:absolute;left:46px;top:40px;display:flex;align-items:center;gap:6px}
  .footer-brand .brand-dot{width:16px;height:16px}
  .footer-brand .brand-name{font-size:14px}
  .contact-list{position:absolute;left:44px;top:131px;list-style:none;font-size:8px;color:var(--muted)}
  .contact-list li{display:flex;align-items:center;gap:5px;height:14.5px}
  .social{position:absolute;left:312px;top:35px;display:flex;flex-direction:column;gap:6px}
  .social span{width:21px;height:21px;border-radius:50%}
  .social .s1{background:#6b3a8c}
  .social .s2{background:var(--blue)}
  .social .s3{background:#222}
  .social .s4{background:var(--blue)}
  .footer-col{position:absolute;top:30px;width:148px}
  .footer-col h3{font-size:9px;font-weight:500;letter-spacing:.3px;padding-left:10px;border-left:2px solid var(--blue);line-height:10px;margin-left:0}
  .footer-col ul{list-style:none;margin-top:9px;border-top:1px solid var(--line)}
  .footer-col li{font-size:8px;color:var(--muted);line-height:14.5px;padding:3px 0;border-bottom:1px solid var(--line)}
  .col-accom{left:373px}
  .col-services{left:537px}
  .copyright-bar{position:absolute;left:0;top:1163px;width:730px;height:37px;background:var(--bar);color:#fff;font-size:9px;font-weight:500;display:flex;align-items:center;justify-content:center}
</style>
</head>
<body>
  <header class="site-header">
    <div class="brand"><span class="brand-dot"></span><span class="brand-name">Tallowcrest Care</span></div>
    <nav class="main-nav">
      <span>HOME</span><span>ABOUT US</span><span class="active">WHAT WE DO ⌄</span><span>REFERRALS</span><span>FEEDBACK</span><span>CONTACT US</span>
    </nav>
  </header>

  <section class="hero">
    <div class="hero-photo" role="img" aria-label="Woman in a wheelchair reading a book in a bright living room"></div>
    <svg class="hero-shape" width="730" height="316" viewBox="0 0 730 316"><path d="M0 0H284Q410 150 271 316H0Z" fill="var(--teal)"/></svg>
    <h1 class="hero-title">Vacancies</h1>
  </section>

  <main class="vacancy-grid">
    <article class="vacancy-card"><div class="vacancy-photo ph-1" role="img" aria-label="Single-storey brick home with driveway and garage"></div><h2 class="vacancy-name">PENRITH</h2><p class="vacancy-meta"><svg width="13" height="11" viewBox="0 0 13 11"><rect x="1" y="1" width="11" height="5" rx="1" fill="none" stroke="#666"/><rect x="0.5" y="6" width="12" height="3" fill="none" stroke="#666"/><path d="M1 9v2M12 9v2" stroke="#666"/></svg>|&nbsp; 4 Bedroom SIL Home</p><a class="book-btn">Book Now</a></article>
    <article class="vacancy-card"><div class="vacancy-photo ph-2" role="img" aria-label="Timber cottage with garden"></div><h2 class="vacancy-name">MOUNT DRUITT</h2><p class="vacancy-meta"><svg width="13" height="11" viewBox="0 0 13 11"><rect x="1" y="1" width="11" height="5" rx="1" fill="none" stroke="#666"/><rect x="0.5" y="6" width="12" height="3" fill="none" stroke="#666"/><path d="M1 9v2M12 9v2" stroke="#666"/></svg>|&nbsp; 4 Bedroom SIL Home</p><a class="book-btn">Book Now</a></article>
    <article class="vacancy-card"><div class="vacancy-photo ph-3" role="img" aria-label="Cream house with tiled roof and lawn"></div><h2 class="vacancy-name">CASULA</h2><p class="vacancy-meta"><svg width="13" height="11" viewBox="0 0 13 11"><rect x="1" y="1" width="11" height="5" rx="1" fill="none" stroke="#666"/><rect x="0.5" y="6" width="12" height="3" fill="none" stroke="#666"/><path d="M1 9v2M12 9v2" stroke="#666"/></svg>|&nbsp; 4 Bedroom SIL Home</p><a class="book-btn">Book Now</a></article>
    <article class="vacancy-card"><div class="vacancy-photo ph-4" role="img" aria-label="Rural property with mountain behind"></div><h2 class="vacancy-name">MOUNT DRUITT</h2><p class="vacancy-meta"><svg width="13" height="11" viewBox="0 0 13 11"><rect x="1" y="1" width="11" height="5" rx="1" fill="none" stroke="#666"/><rect x="0.5" y="6" width="12" height="3" fill="none" stroke="#666"/><path d="M1 9v2M12 9v2" stroke="#666"/></svg>|&nbsp; 4 Bedroom SIL Home</p><a class="book-btn">Book Now</a></article>
    <article class="vacancy-card"><div class="vacancy-photo ph-5" role="img" aria-label="Dark timber two-storey house with garden"></div><h2 class="vacancy-name">EASTWOOD</h2><p class="vacancy-meta"><svg width="13" height="11" viewBox="0 0 13 11"><rect x="1" y="1" width="11" height="5" rx="1" fill="none" stroke="#666"/><rect x="0.5" y="6" width="12" height="3" fill="none" stroke="#666"/><path d="M1 9v2M12 9v2" stroke="#666"/></svg>|&nbsp; 4 Bedroom SIL Home</p><a class="book-btn">Book Now</a></article>
    <article class="vacancy-card"><div class="vacancy-photo ph-6" role="img" aria-label="Suburban home with palm tree and double garage"></div><h2 class="vacancy-name">BAULKHAM HILLS</h2><p class="vacancy-meta"><svg width="13" height="11" viewBox="0 0 13 11"><rect x="1" y="1" width="11" height="5" rx="1" fill="none" stroke="#666"/><rect x="0.5" y="6" width="12" height="3" fill="none" stroke="#666"/><path d="M1 9v2M12 9v2" stroke="#666"/></svg>|&nbsp; 4 Bedroom SIL Home</p><a class="book-btn">Book Now</a></article>
    <article class="vacancy-card"><div class="vacancy-photo ph-7" role="img" aria-label="Red brick home with lawn and long driveway"></div><h2 class="vacancy-name">MERRYLANDS</h2><p class="vacancy-meta"><svg width="13" height="11" viewBox="0 0 13 11"><rect x="1" y="1" width="11" height="5" rx="1" fill="none" stroke="#666"/><rect x="0.5" y="6" width="12" height="3" fill="none" stroke="#666"/><path d="M1 9v2M12 9v2" stroke="#666"/></svg>|&nbsp; 4 Bedroom SIL Home</p><a class="book-btn">Book Now</a></article>
    <article class="vacancy-card"><div class="vacancy-photo ph-8" role="img" aria-label="Stone house with chimney and flowering shrubs"></div><h2 class="vacancy-name">BAULKHAM HILLS</h2><p class="vacancy-meta"><svg width="13" height="11" viewBox="0 0 13 11"><rect x="1" y="1" width="11" height="5" rx="1" fill="none" stroke="#666"/><rect x="0.5" y="6" width="12" height="3" fill="none" stroke="#666"/><path d="M1 9v2M12 9v2" stroke="#666"/></svg>|&nbsp; 4 Bedroom SIL Home</p><a class="book-btn">Book Now</a></article>
  </main>

  <footer class="site-footer">
    <div class="footer-brand"><span class="brand-dot"></span><span class="brand-name">Tallowcrest Care</span></div>
    <ul class="contact-list">
      <li><svg width="9" height="8" viewBox="0 0 9 8"><rect x="0.5" y="0.5" width="8" height="7" fill="none" stroke="var(--pink)"/><path d="M0.5 1l4 3 4-3" fill="none" stroke="var(--pink)"/></svg>Email: info@tallowcrestcare.com.au</li>
      <li><svg width="9" height="9" viewBox="0 0 9 9"><path d="M1 1.5L2.8 1l1 2-1 .8a5 5 0 0 0 2.4 2.4l.8-1 2 1L7.5 8C4 8 1 5 1 1.5z" fill="var(--pink)"/></svg>Phone: +61 0400 555 218</li>
      <li><svg width="9" height="9" viewBox="0 0 9 9"><circle cx="4.5" cy="4.5" r="4" fill="none" stroke="var(--pink)"/><path d="M4.5 2v2.7L6.3 5.6" fill="none" stroke="var(--pink)"/></svg>Operating Hours: 9AM To 5PM Monday - Friday</li>
    </ul>
    <div class="social"><span class="s1"></span><span class="s2"></span><span class="s3"></span><span class="s4"></span></div>
    <div class="footer-col col-accom">
      <h3>ACCOMMODATION</h3>
      <ul>
        <li>Supported Independent Living (SIL)</li>
        <li>Specialist Disability Accommodation (SDA)</li>
        <li>Short term Accommodation (Respite)</li>
        <li>Vacancies</li>
      </ul>
    </div>
    <div class="footer-col col-services">
      <h3>WHAT WE DO</h3>
      <ul>
        <li>In Home Care</li>
        <li>Social &amp; Community Services</li>
        <li>Therapeutic Supports</li>
        <li>Support Coordination</li>
        <li>Home Modifications</li>
      </ul>
    </div>
  </footer>
  <div class="copyright-bar">© Copyright 2024 | Tallowcrest Care | All Rights Reserved.</div>
</body>
</html>
```